Harrow Grading LLC business card design

Excavation company business cards

Contact Information for Business Card

Harrow Grading LLC cell phone 208-417-6290 office phone 208-319-4856 harrowgradingllc@maplecove.com Driveways, site prep, retaining walls, septic systems, rock delivery

Colors

Designer to choose colors to be used in the design.

```html
<!DOCTYPE html>
<html lang="en">
<head>
<meta charset="utf-8">
<title>Harrow Grading LLC – Business Card</title>
<link href="https://fonts.googleapis.com/css2?family=Montserrat:wght@400;500;700;800&display=swap" rel="stylesheet">
<style>
  :root {
    --page-bg: #d9d6d2;
    --card-bg: #1f1f1f;
    --card-edge: #2a2a2a;
    --accent: #f07a22;
    --text-light: #f2f2f2;
    --text-muted: #cfcfcf;
  }
  * { box-sizing: border-box; margin: 0; padding: 0; }
  html, body {
    width: 1200px; height: 912px; overflow: hidden;
    background: var(--page-bg);
    font-family: "Montserrat", sans-serif;
  }
  .canvas { position: relative; width: 1200px; height: 912px; }
  .card {
    position: absolute; width: 560px; height: 320px;
    background: var(--card-bg);
    border: 1px solid var(--card-edge);
    box-shadow: 0 10px 30px rgba(0,0,0,.28);
    overflow: hidden;
  }
  .card--front { left: 60px; top: 80px; display: flex; align-items: center; justify-content: center; gap: 16px; }
  .card--back { left: 580px; top: 500px; }

  .brand-mark { width: 22px; height: 22px; background: var(--accent); flex: none; }
  .brand-name {
    color: var(--accent); font-weight: 800; letter-spacing: 1px;
    text-transform: uppercase; font-size: 34px; line-height: 1;
  }
  .card--back .brand-name {
    position: absolute; left: 0; right: 0; top: 46px;
    text-align: center; font-size: 30px;
  }

  .services {
    position: absolute; right: 300px; top: 140px; text-align: right;
  }
  .services__title { color: var(--accent); font-weight: 700; font-size: 17px; margin-bottom: 6px; }
  .services__list { list-style: none; color: var(--text-light); font-size: 15px; line-height: 1.28; }

  .divider { position: absolute; left: 278px; top: 138px; width: 2px; height: 140px; background: var(--accent); }

  .contact { position: absolute; left: 298px; top: 136px; }
  .contact__name { color: var(--accent); font-weight: 800; font-size: 21px; text-transform: uppercase; }
  .contact__role { color: var(--text-light); font-size: 15px; margin-bottom: 12px; }
  .contact__list { list-style: none; color: var(--text-light); font-size: 13px; line-height: 1.7; }
  .contact__item { display: flex; align-items: center; gap: 7px; }
  .contact__icon { width: 11px; height: 11px; flex: none; }
</style>
</head>
<body>
<main class="canvas">
  <section class="card card--front" aria-label="Card front">
    <span class="brand-mark"></span>
    <span class="brand-name">Harrow Grading LLC</span>
  </section>

  <section class="card card--back" aria-label="Card back">
    <div class="brand-name">Harrow Grading LLC</div>

    <div class="services">
      <p class="services__title">Harrow Grading LLC</p>
      <ul class="services__list">
        <li>Driveways</li>
        <li>site prep</li>
        <li>retaining walls</li>
        <li>septic systems</li>
        <li>rock delivery</li>
      </ul>
    </div>

    <div class="divider"></div>

    <div class="contact">
      <p class="contact__name">Dale Whitmore</p>
      <p class="contact__role">Director</p>
      <ul class="contact__list">
        <li class="contact__item">
          <svg class="contact__icon" viewBox="0 0 12 12"><rect x="3" y="0.5" width="6" height="11" rx="1.2" fill="none" stroke="#f07a22" stroke-width="1.2"/><line x1="5" y1="9.5" x2="7" y2="9.5" stroke="#f07a22" stroke-width="1"/></svg>
          208-417-6290
        </li>
        <li class="contact__item">
          <svg class="contact__icon" viewBox="0 0 12 12"><path d="M1 4c0-2 2-2.5 5-2.5S11 2 11 4l-2.5.6L8 3.4H4l-.5 1.2L1 4z" fill="#f07a22"/><rect x="2.5" y="5.5" width="7" height="5.5" rx="1" fill="#f07a22"/></svg>
          208-319-4856
        </li>
        <li class="contact__item">
          <svg class="contact__icon" viewBox="0 0 12 12"><rect x="0.6" y="2.2" width="10.8" height="7.6" fill="none" stroke="#f07a22" stroke-width="1.1"/><path d="M0.8 2.5 6 6.6l5.2-4.1" fill="none" stroke="#f07a22" stroke-width="1.1"/></svg>
          harrowgradingllc@maplecove.com
        </li>
      </ul>
    </div>
  </section>
</main>
</body>
</html>
```